Business Card - high end, modern health care

Hey designers!

We need a double sided business card for the boutique, cutting edge physical therapy rehabilitation centre in Sydney's Northern Beaches.

With the most qualified physios in the area The Harbourview Motion Clinic does what other physiotherapy practices do not, we take our time with our patients giving them longer appointments, better physios and therefor faster results!

We guarantee that the service people receive at THMC will be unparalleled.

Hence we need a business card to reflect our modern, boutique, high end service. The final design needs to reflect that we are in a class of our own yet with the feel of beachside retreat.

Below I have attached our logo in both blue on white and white on blue. The exact colour is;
and the font that we have used in our logo is Tex Gyre Aventador.

I like the idea of the blue as the main colour as it is more eye catching and our signage onto the main road will be in this blue and in the interest of consistency across marketing the blue needs to be a part of the design. However I would appreciate a few designs onto a wooden background as this is a visual theme within the fitout of the practice.

The design needs to be of standard size (91x55mm).

Target Market(s)

We target people who have an end outcome in mind and those who have had poor experiences with other providers and ensure that everyone gets the care that they deserve with a premium service that is tailored to the individuals circumstances. As a premium service, the target market is highly educated, business and tech savvy with the additional target market of elderly people who have self funded their retirement and see value in paying for the best ongoing rehabilitation to maintain independence.

Industry/Entity Type

Physical Therapy

Contact Information for Business Card

Name, designation( Titled Musculoskeletal Physiotherapist... there will also be those in the company that have multiple designations ie 5 or 6 words long), phone number, email, facebook, instagram, address

Font styles to use
Sans Serif

Colors

Designer to choose colors to be used in the design.

Requirements
Must have
• Front - The logo as large as possible, blue or wooden theme, and all of the important details.
• Back - A blank space/lines on which to write appointment times (no "Appointment, date, time" etc.)
Nice to have
• facebook url
• logos for facebook and instagram
• Mini logos for the phone and email?

```html
<!DOCTYPE html>
<html lang="en">
<head>
<meta charset="utf-8">
<title>The Harbourview Motion Clinic – Business Card</title>
<link rel="stylesheet" href="https://fonts.googleapis.com/css2?family=Questrial&display=swap">
<style>
  :root {
    --brand-blue: #1057ab;
    --brand-blue-soft: #2f6cb8;
    --paper: #ffffff;
    --ink: #1c1c1c;
    --ink-muted: #555a60;
    --rule: #4a4a4a;
    --rule-light: #b9bcc0;
    --edge-grey: #d9dadc;
    --backdrop: #e9ebee;
    --social-fb: #1a8fd8;
    --social-ig: #e0559a;
  }
  * { box-sizing: border-box; margin: 0; padding: 0; }
  html, body {
    width: 1200px; height: 1200px; overflow: hidden;
    background: var(--backdrop);
    font-family: "Questrial", "Helvetica Neue", Arial, sans-serif;
  }
  .sheet {
    width: 1200px; height: 1200px;
    display: flex; flex-direction: column; align-items: center; justify-content: center;
    gap: 40px;
  }
  .card {
    position: relative;
    width: 900px; height: 544px;
    border-radius: 40px;
    overflow: hidden;
    box-shadow: 0 6px 18px rgba(0,0,0,.12);
  }

  /* Logo side */
  .card--logo { background: var(--brand-blue); }
  .card--logo .halo {
    position: absolute; left: 330px; top: 52px;
    width: 440px; height: 440px; border-radius: 50%;
    background: var(--brand-blue-soft); opacity: .55;
  }
  .wordmark {
    position: absolute; display: flex; align-items: center; gap: 18px;
    color: var(--paper); text-transform: uppercase;
  }
  .card--logo .wordmark { left: 50%; top: 50%; transform: translate(-50%, -50%); }
  .wordmark .dot { width: 74px; height: 74px; border-radius: 50%; background: currentColor; flex: none; }
  .wordmark .name { font-size: 38px; line-height: 1.12; letter-spacing: 3px; }

  /* Details side */
  .card--details { background: var(--paper); color: var(--ink); }
  .card--details .wordmark { right: 58px; top: 58px; color: var(--brand-blue); gap: 10px; }
  .card--details .wordmark .dot { width: 38px; height: 38px; }
  .card--details .wordmark .name { font-size: 19px; letter-spacing: 1.5px; line-height: 1.15; }

  .rule { position: absolute; height: 2px; background: var(--rule); }
  .rule--top { left: 90px; right: 58px; top: 150px; }
  .rule--mid { left: 90px; right: 58px; top: 268px; }
  .rule--low { left: 90px; width: 470px; top: 378px; }

  .person { position: absolute; left: 90px; top: 176px; }
  .person .full-name { font-size: 40px; line-height: 1.1; }
  .person .full-name em { font-style: normal; color: var(--brand-blue); }
  .person .role { font-size: 20px; color: var(--ink-muted); margin-top: 6px; }

  .socials { position: absolute; right: 58px; top: 172px; list-style: none; }
  .socials li { display: flex; align-items: center; gap: 12px; font-size: 20px; margin-bottom: 12px; }
  .socials .chip { width: 26px; height: 26px; border-radius: 50%; }
  .chip--fb { background: var(--social-fb); }
  .chip--ig { background: var(--social-ig); }

  .contacts { position: absolute; left: 90px; top: 290px; list-style: none; }
  .contacts li { display: flex; align-items: center; gap: 16px; font-size: 23px; margin-bottom: 14px; }
  .contacts svg { width: 28px; height: 28px; flex: none; }

  .write-line {
    position: absolute; left: 90px; right: 58px; top: 450px;
    border-top: 2px dashed var(--rule-light);
  }
  .write-line--upper { top: 412px; left: 620px; }

  .band { position: absolute; right: 0; bottom: 0; }
</style>
</head>
<body>
<main class="sheet">

  <section class="card card--logo" aria-label="Card front">
    <div class="halo"></div>
    <div class="wordmark">
      <span class="dot"></span>
      <span class="name">The Harbourview<br>Motion Clinic</span>
    </div>
  </section>

  <section class="card card--details" aria-label="Card back">
    <div class="wordmark">
      <span class="dot"></span>
      <span class="name">The Harbourview<br>Motion Clinic</span>
    </div>

    <div class="rule rule--top"></div>

    <div class="person">
      <p class="full-name">Name of <em>Person</em></p>
      <p class="role">Designation</p>
    </div>

    <ul class="socials">
      <li><span class="chip chip--fb"></span>facebook/name</li>
      <li><span class="chip chip--ig"></span>instagram_name</li>
    </ul>

    <div class="rule rule--mid"></div>

    <ul class="contacts">
      <li>
        <svg viewBox="0 0 28 28" aria-hidden="true"><circle cx="14" cy="14" r="12" fill="none" stroke="#1c1c1c" stroke-width="2.4"/><path d="M10 8.5c-1.3 1-1.2 3 .5 5.6s3.9 4.4 5.7 4.3c1 0 1.7-.6 2-1.2l-2.2-1.9-1.4.9c-1-.5-2.3-1.9-2.8-3l.9-1.4L11 8.3z" fill="#1c1c1c"/></svg>
        555.014.2297
      </li>
      <li>
        <svg viewBox="0 0 28 28" aria-hidden="true"><rect x="2" y="6" width="24" height="16" fill="#1c1c1c"/><path d="M3 7l11 8 11-8" fill="none" stroke="#fff" stroke-width="1.6"/></svg>
        companyname@email.com
      </li>
    </ul>

    <div class="rule rule--low"></div>
    <div class="write-line write-line--upper"></div>
    <div class="write-line"></div>

    <svg class="band" width="900" height="544" viewBox="0 0 900 544" aria-hidden="true">
      <path d="M0 544 L0 520 L560 520 L560 544 Z" fill="var(--edge-grey)"/>
      <path d="M560 544 L560 470 Q560 420 610 420 L900 420 L900 544 Z" fill="var(--edge-grey)"/>
      <path d="M590 544 L590 478 Q590 440 630 440 L900 440 L900 544 Z" fill="var(--brand-blue)"/>
    </svg>
  </section>

</main>
</body>
</html>
```